Oil and Gas Exploration and Production company needs a business card design

We need a business card design using our logo and colors in the logo. We want a mainstream design.

```html
<!DOCTYPE html>
<html lang="en">
<head>
<meta charset="utf-8">
<title>Solara Oil &amp; Gas – Business Card</title>
<link rel="stylesheet" href="https://fonts.googleapis.com/css2?family=Roboto+Slab:wght@800&family=Open+Sans:wght@400;700&display=swap">
<style>
  :root {
    --backdrop: #2b2b2d;
    --paper: #ffffff;
    --gold: #c99a2e;
    --ink: #221f1f;
    --grey: #5a5a5a;
    --white: #ffffff;
  }
  * { box-sizing: border-box; margin: 0; padding: 0; }
  html, body { width: 1200px; height: 900px; overflow: hidden; }
  body {
    background: var(--backdrop);
    font-family: "Open Sans", Arial, sans-serif;
    position: relative;
  }
  .card {
    position: absolute;
    left: 290px;
    width: 620px;
    height: 354px;
    overflow: hidden;
    box-shadow: 0 10px 30px rgba(0,0,0,.45);
  }
  .card--front { top: 80px; background: var(--paper); }
  .card--back { top: 470px; background: var(--gold); }

  /* front */
  .brand {
    position: absolute;
    top: 120px;
    left: 0; right: 0;
    display: flex;
    justify-content: center;
    align-items: center;
    gap: 14px;
  }
  .brand__dot {
    width: 30px; height: 30px;
    border-radius: 50%;
    background: var(--gold);
  }
  .brand__name {
    font-family: "Roboto Slab", Georgia, serif;
    font-weight: 800;
    font-size: 48px;
    color: var(--ink);
    letter-spacing: 0.5px;
  }
  .front__web {
    position: absolute;
    top: 240px; left: 0; right: 0;
    text-align: center;
    font-size: 14px;
    letter-spacing: 7px;
    color: var(--grey);
  }

  /* back */
  .back__corner {
    position: absolute;
    left: 0; bottom: 0;
    width: 300px; height: 300px;
  }
  .person {
    position: absolute;
    left: 360px; top: 62px;
  }
  .person__name {
    font-weight: 700;
    font-size: 19px;
    color: var(--ink);
    letter-spacing: .3px;
  }
  .person__role {
    font-size: 13px;
    color: var(--white);
    letter-spacing: .5px;
  }
  .contact {
    position: absolute;
    left: 360px; top: 168px;
    list-style: none;
    color: var(--white);
    font-size: 13px;
    line-height: 21px;
  }
  .contact li { display: flex; align-items: center; gap: 10px; }
  .contact .icon { width: 13px; height: 13px; flex: none; }
  .contact .no-icon { padding-left: 23px; }
</style>
</head>
<body>

<section class="card card--front">
  <div class="brand">
    <span class="brand__dot"></span>
    <span class="brand__name">Solara Oil &amp; Gas</span>
  </div>
  <p class="front__web">www.solaraoilgas.com</p>
</section>

<section class="card card--back">
  <svg class="back__corner" viewBox="0 0 300 300" aria-hidden="true">
    <circle cx="30" cy="300" r="250" fill="var(--ink)" stroke="var(--white)" stroke-width="4"/>
  </svg>

  <div class="person">
    <p class="person__name">MARK ELLISON</p>
    <p class="person__role">PRESIDENT</p>
  </div>

  <ul class="contact">
    <li class="no-icon">4127 Harbor View Lane</li>
    <li class="no-icon">Brookdale, NY 11020</li>
    <li>
      <svg class="icon" viewBox="0 0 16 16"><path fill="var(--ink)" d="M3 1l3 3-2 2c1 2 3 4 5 5l2-2 3 3-2 3C7 15 1 9 0 4z"/></svg>
      555 0142 2253
    </li>
    <li>
      <svg class="icon" viewBox="0 0 16 16"><rect x="4" y="1" width="8" height="14" rx="1.5" fill="var(--ink)"/><rect x="5.5" y="3" width="5" height="8" fill="var(--gold)"/></svg>
      555 0187 5335
    </li>
    <li>
      <svg class="icon" viewBox="0 0 16 16"><rect x="1" y="6" width="14" height="8" rx="1" fill="var(--ink)"/><rect x="4" y="1" width="8" height="5" fill="var(--ink)"/></svg>
      555 0163 3856
    </li>
    <li>
      <svg class="icon" viewBox="0 0 16 16"><rect x="1" y="3" width="14" height="10" fill="var(--ink)"/><path d="M1 3l7 6 7-6" stroke="var(--gold)" stroke-width="1.2" fill="none"/></svg>
      info@solaraoilgas.com
    </li>
    <li>
      <svg class="icon" viewBox="0 0 16 16"><circle cx="8" cy="8" r="7" fill="var(--ink)"/><path d="M1 8h14M8 1c3 3 3 11 0 14M8 1c-3 3-3 11 0 14" stroke="var(--gold)" stroke-width="1" fill="none"/></svg>
      www.solaraoilgas.com
    </li>
  </ul>
</section>

</body>
</html>
```